Telecommunications/Power civil contractor needs business card design

Were a new telecommunications/power underground civil contractor that is looking for a new business card design. Our company colours are silver or grey and orange. Feel free to use the white background logo or the black background logo.

Target Market(s)

Local contractors, utility companies, private sector mining/energy companies, developers.

Industry/Entity Type

Telecommunications

Contact Information for Business Card

Each card will need the following info:
Persons name:
Title:
E-mail:
Phone number:
Shop Address:
Mailing Address:

Requirements
Must have
• Each card will need the following info:
• Persons name:
• Title:
• E-mail:
• Phone number:
• Shop Address:
• Mailing Address:

```html
<!DOCTYPE html>
<html lang="en">
<head>
<meta charset="utf-8">
<title>Ridgeline Contracting Inc — Business Card</title>
<link href="https://fonts.googleapis.com/css2?family=Open+Sans:wght@400;600;700&display=swap" rel="stylesheet">
<style>
  :root {
    --orange: #f05a22;
    --grey: #6d6e71;
    --black: #0b0b0b;
    --white: #ffffff;
    --backdrop: #e6e3de;
  }
  * { margin: 0; padding: 0; box-sizing: border-box; }
  html, body { width: 1200px; height: 675px; overflow: hidden; }
  body {
    background: var(--backdrop);
    font-family: "Open Sans", Arial, sans-serif;
    position: relative;
  }
  .card {
    position: absolute;
    top: 190px;
    width: 504px;
    height: 288px;
    box-shadow: 0 6px 18px rgba(0,0,0,0.18);
    overflow: hidden;
  }
  .card-back { left: 64px; background: var(--black); }
  .card-front { left: 632px; background: var(--white); }

  .brand {
    position: absolute;
    display: flex;
    align-items: center;
    gap: 10px;
  }
  .brand-mark {
    width: 34px; height: 34px;
    border-radius: 50%;
    border: 3px solid var(--grey);
    flex: none;
  }
  .brand-name {
    font-weight: 700;
    font-size: 17px;
    line-height: 1.1;
    letter-spacing: 0.5px;
    color: var(--orange);
    text-transform: uppercase;
  }
  .card-back .brand { left: 50%; top: 50%; transform: translate(-50%, -50%); }
  .card-front .brand { left: 28px; top: 52px; }

  .contact-panel {
    position: absolute;
    top: 0; right: 0;
    width: 236px; height: 100%;
    background: var(--orange);
    color: var(--white);
    padding: 124px 10px 0 18px;
    font-size: 11.5px;
  }
  .panel-edge {
    position: absolute;
    left: 260px; top: 140px;
    width: 8px; height: 148px;
    background: var(--grey);
  }
  .person-name { font-weight: 700; font-size: 16px; letter-spacing: 0.4px; }
  .person-title { margin-bottom: 12px; }
  .address { line-height: 1.35; margin-bottom: 10px; }
  .contact-line {
    display: flex; align-items: center; gap: 6px;
    line-height: 1.5;
    white-space: nowrap;
  }
  .contact-line svg { width: 12px; height: 12px; flex: none; }
</style>
</head>
<body>
  <section class="card card-back" aria-label="Card back">
    <div class="brand">
      <span class="brand-mark"></span>
      <span class="brand-name">Ridgeline<br>Contracting Inc</span>
    </div>
  </section>

  <section class="card card-front" aria-label="Card front">
    <div class="brand">
      <span class="brand-mark"></span>
      <span class="brand-name">Ridgeline<br>Contracting Inc</span>
    </div>
    <div class="panel-edge"></div>
    <div class="contact-panel">
      <p class="person-name">DORIAN VALE</p>
      <p class="person-title">Managing Director</p>
      <p class="address">N. 8 Alder Street,<br>Suite 200, Tacoma, WA 55555</p>
      <p class="contact-line">
        <svg viewBox="0 0 12 12" aria-hidden="true"><path d="M2.5 1 L4.5 1 L5.2 3.5 L4 4.5 Q5 7 7.5 8 L8.5 6.8 L11 7.5 L11 9.5 Q10.5 11 9 11 Q1 10 1 3 Q1 1.5 2.5 1 Z" fill="#fff"/></svg>
        555.010.2030
      </p>
      <p class="contact-line">
        <svg viewBox="0 0 12 12" aria-hidden="true"><rect x="1" y="2.5" width="10" height="7" rx="1" fill="#fff"/><path d="M1.5 3 L6 6.5 L10.5 3" stroke="#f05a22" stroke-width="1" fill="none"/></svg>
        info@ridgelinecontracting.com
      </p>
    </div>
  </section>
</body>
</html>
```